Business Card For Halvenmoor Financial Consulting

Hi, I would like a business card designed. Bold, modern.
Please use the same design as the logo. I have also attached the website design to see the overall theme.
Wordmark Font
Color: Hex: #01AEF7

```html
<!DOCTYPE html>
<html lang="en">
<head>
<meta charset="utf-8">
<title>Halvenmoor Financial Consulting – Business Card</title>
<link rel="stylesheet" href="https://fonts.googleapis.com/css2?family=Roboto:wght@400;700&display=swap">
<style>
  :root {
    --backdrop: #3b3b3b;
    --card: #17222d;
    --card-back: #16212b;
    --accent: #01aef7;
    --text: #e8edf2;
    --muted: #8fa3b5;
    --mark: #4e6f8f;
  }
  * { box-sizing: border-box; margin: 0; padding: 0; }
  html, body { width: 1200px; height: 801px; overflow: hidden; }
  body {
    background: var(--backdrop);
    font-family: "Roboto", Arial, sans-serif;
    display: flex;
    align-items: center;
    justify-content: center;
    gap: 40px;
  }
  .card {
    width: 520px;
    height: 297px;
    border-bottom: 3px solid var(--accent);
    position: relative;
  }
  .card--front { background: var(--card); display: flex; align-items: center; }
  .card--back { background: var(--card-back); display: flex; align-items: center; justify-content: center; }

  .brand { width: 250px; padding-left: 34px; display: flex; align-items: center; gap: 10px; }
  .brand__square { width: 22px; height: 22px; border: 2px solid var(--accent); flex: none; }
  .brand__name { color: var(--text); font-weight: 700; font-size: 15px; letter-spacing: 1.5px; line-height: 1.25; text-transform: uppercase; }

  .divider { width: 1px; height: 120px; background: var(--accent); margin-right: 20px; }

  .contact { color: var(--text); font-size: 12.5px; line-height: 1.45; }
  .contact__name { color: var(--accent); font-weight: 700; font-size: 17px; text-transform: uppercase; letter-spacing: .3px; }
  .contact__title { margin-bottom: 10px; }
  .contact__address { margin-bottom: 10px; }
  .contact__line { display: flex; align-items: center; gap: 6px; }
  .contact__line svg { width: 10px; height: 10px; flex: none; fill: var(--accent); }

  .back-brand { display: flex; align-items: center; gap: 12px; }
  .back-brand__square { width: 30px; height: 30px; border: 3px solid var(--mark); }
  .back-brand__name { color: var(--mark); font-weight: 700; font-size: 18px; letter-spacing: 2px; text-transform: uppercase; }
</style>
</head>
<body>
  <section class="card card--front">
    <div class="brand">
      <span class="brand__square"></span>
      <span class="brand__name">Halvenmoor<br>Consulting</span>
    </div>
    <div class="divider"></div>
    <div class="contact">
      <p class="contact__name">Corin Maddox</p>
      <p class="contact__title">President</p>
      <p class="contact__address">1870 Linden Cove Drive<br>Harbor Vale CA 90417</p>
      <p class="contact__line">
        <svg viewBox="0 0 10 10" aria-hidden="true"><path d="M2 0.5 L3.8 2.6 L2.9 3.8 Q4.2 6 6.2 7.1 L7.4 6.2 L9.5 8 L8.3 9.5 Q4.5 9.5 0.5 1.7 Z"/></svg>
        555-014-2270
      </p>
      <p class="contact__line">
        <svg viewBox="0 0 10 10" aria-hidden="true"><path d="M0.5 2 H9.5 V8.5 H0.5 Z M1 2.4 L5 5.6 L9 2.4" stroke="#17222d" stroke-width=".8"/></svg>
        info@HalvenmoorConsulting.com
      </p>
      <p class="contact__line">
        <svg viewBox="0 0 10 10" aria-hidden="true"><circle cx="5" cy="5" r="4.5"/></svg>
        www.HalvenmoorConsulting.com
      </p>
    </div>
  </section>

  <section class="card card--back">
    <div class="back-brand">
      <span class="back-brand__square"></span>
      <span class="back-brand__name">Halvenmoor</span>
    </div>
  </section>
</body>
</html>
```